Thornvale Group needs a business card design

We need a new business card design using the logo recently selected in a logo competition on Pixel Bazaar. Our business is a consultancy specializing in aviation and energy and the winning business card design will promote an image of precision and professionalism with creativity.

Please use the logo with the name on the front of the card and use a complementary font. Make the back white with either the light grey or dark grey logo.

Target Market(s)

Senior finance and legal leaders at aviation and energy companies

Industry/Entity Type

Management Consulting

Contact Information for Business Card

Peter Castrell
President
Thornvale Group

www.thornvalegroup.example

(555) 204-6391
pc@thornvalegroup.example

Requirements
Must have
• Professional font that goes well with the logo font

```html
<!DOCTYPE html>
<html lang="en">
<head>
<meta charset="utf-8">
<title>Thornvale Group – Business Card</title>
<link href="https://fonts.googleapis.com/css2?family=Open+Sans:wght@400;600&display=swap" rel="stylesheet">
<style>
  :root {
    --navy: #0f3e6e;
    --band-grey: #5f6062;
    --paper: #ffffff;
    --backdrop: #e8e5e2;
    --ink-light: #ffffff;
  }
  html, body {
    margin: 0;
    padding: 0;
    width: 1200px;
    height: 900px;
    overflow: hidden;
    background: var(--backdrop);
    font-family: "Open Sans", Arial, sans-serif;
  }
  .stage {
    position: relative;
    width: 1200px;
    height: 900px;
  }
  .card {
    position: absolute;
    background: var(--paper);
    overflow: hidden;
    box-shadow: 0 6px 18px rgba(0,0,0,0.12);
  }
  .card--front {
    left: 77px;
    top: 34px;
    width: 589px;
    height: 364px;
  }
  .card--back {
    left: 388px;
    top: 505px;
    width: 567px;
    height: 352px;
  }
  .card__bands {
    position: absolute;
    left: 0;
    top: 0;
    width: 100%;
    height: 100%;
  }
  .brand {
    position: absolute;
    left: 0;
    width: 100%;
    display: flex;
    justify-content: center;
    align-items: center;
    gap: 14px;
    color: var(--navy);
    font-weight: 400;
    letter-spacing: 3px;
    text-transform: uppercase;
  }
  .brand__mark {
    width: 22px;
    height: 22px;
    background: var(--navy);
  }
  .card--front .brand { top: 128px; font-size: 28px; }
  .card--back .brand { top: 196px; font-size: 28px; }
  .holder {
    position: absolute;
    right: 351px;
    top: 266px;
    text-align: right;
    color: var(--ink-light);
  }
  .holder__name {
    font-size: 20px;
    font-weight: 600;
    line-height: 1.2;
  }
  .holder__title {
    font-size: 15px;
    font-weight: 400;
    margin-top: 4px;
  }
  .contact {
    position: absolute;
    left: 276px;
    top: 271px;
    color: var(--ink-light);
    font-size: 15px;
    list-style: none;
    margin: 0;
    padding: 0;
  }
  .contact__item {
    display: flex;
    align-items: center;
    gap: 9px;
    height: 25px;
  }
  .contact__icon { width: 13px; height: 13px; flex: none; }
</style>
</head>
<body>
<main class="stage">
  <section class="card card--front" aria-label="Business card front">
    <svg class="card__bands" viewBox="0 0 589 364" aria-hidden="true">
      <polygon points="0,216 406,216 381,241 0,241" fill="var(--band-grey)"/>
      <polygon points="416,206 589,206 589,364 0,364 0,245 384,245" fill="var(--navy)"/>
    </svg>
    <div class="brand"><span class="brand__mark"></span>Thornvale Group</div>
    <div class="holder">
      <div class="holder__name">Peter J. Castrell</div>
      <div class="holder__title">President</div>
    </div>
    <ul class="contact">
      <li class="contact__item">
        <svg class="contact__icon" viewBox="0 0 24 24" aria-hidden="true"><path fill="#fff" d="M6.6 10.8a15 15 0 0 0 6.6 6.6l2.2-2.2c.3-.3.7-.4 1-.2 1.1.4 2.3.6 3.6.6.6 0 1 .4 1 1V20c0 .6-.4 1-1 1A17 17 0 0 1 3 4c0-.6.4-1 1-1h3.5c.6 0 1 .4 1 1 0 1.3.2 2.5.6 3.6.1.3 0 .7-.2 1z"/></svg>
        <span>(555) 204-6391</span>
      </li>
      <li class="contact__item">
        <svg class="contact__icon" viewBox="0 0 24 24" aria-hidden="true"><path fill="#fff" d="M2 5h20v14H2z"/><path fill="none" stroke="var(--navy)" stroke-width="2" d="M2 5l10 8 10-8"/></svg>
        <span>pc@thornvalegroup.example</span>
      </li>
    </ul>
  </section>

  <section class="card card--back" aria-label="Business card back">
    <div class="brand"><span class="brand__mark"></span>Thornvale Group</div>
  </section>
</main>
</body>
</html>
```